Professional & attention grabbing.

A business card design, front and back. I already have a logo I will attach, but I am open to something new as well.
Things to include:
Name:
Title:
Phone:
Email:
Wanting something that is professional but attention grabbing.
Also we do a lot of work using drones on natural gas pipelines (leading the future)if you want to include any of that. I'm open to ideas.
Target Market(s)
Natural gas transmission industry / greenhouse gas mitigation industry
Industry/Entity Type
Business
Colors
Designer to choose colors to be used in the design.
Look and feel
Each slider illustrates characteristics of the customer's brand and the style your logo design should communicate.

```html
<!DOCTYPE html>
<html lang="en">
<head>
<meta charset="utf-8">
<title>KV Field Inspections – Business Card</title>
<link rel="stylesheet" href="https://fonts.googleapis.com/css2?family=Titillium+Web:wght@400;600&display=swap">
<style>
  :root {
    --page-bg: #d9d6d2;
    --card-light: #eeeeee;
    --card-mid: #d7d7d7;
    --band-dark: #1f1f1f;
    --band-mid: #2c2c2c;
    --band-fade: #7d7d7d;
    --accent-red: #9e1b1f;
    --text-light: #e6e6e6;
    --text-dark: #1c1c1c;
  }
  html, body {
    margin: 0;
    width: 1200px;
    height: 969px;
    overflow: hidden;
    background: var(--page-bg);
  }
  .canvas {
    position: relative;
    width: 1200px;
    height: 969px;
  }
  .card {
    position: absolute;
    left: 100px;
    top: 200px;
    width: 1000px;
    height: 569px;
    border-radius: 36px;
    overflow: hidden;
    background: linear-gradient(160deg, var(--card-light), var(--card-mid));
    box-shadow: 0 12px 40px rgba(0,0,0,0.18);
    font-family: "Titillium Web", sans-serif;
  }
  .accent-line {
    position: absolute;
    left: 0;
    right: 0;
    top: 222px;
    height: 6px;
    background: var(--accent-red);
  }
  .dark-band {
    position: absolute;
    left: 0;
    right: 0;
    top: 234px;
    bottom: 0;
    background: linear-gradient(160deg, var(--band-dark) 0%, var(--band-mid) 65%, var(--band-fade) 100%);
  }
  .brand {
    position: absolute;
    left: 500px;
    top: 96px;
    display: flex;
    align-items: center;
    gap: 14px;
  }
  .brand-square {
    width: 30px;
    height: 30px;
    background: var(--accent-red);
  }
  .brand-name {
    font-size: 34px;
    font-weight: 600;
    color: var(--text-dark);
    letter-spacing: 1px;
    text-transform: uppercase;
    white-space: nowrap;
  }
  .person {
    position: absolute;
    left: 62px;
    top: 290px;
  }
  .person-name {
    margin: 0;
    font-size: 34px;
    font-weight: 600;
    color: var(--accent-red);
    letter-spacing: 1px;
    line-height: 1.1;
  }
  .person-title {
    margin: 6px 0 0;
    font-size: 26px;
    font-weight: 400;
    color: var(--text-light);
  }
  .contact {
    position: absolute;
    left: 62px;
    top: 402px;
    margin: 0;
    padding: 0;
    list-style: none;
  }
  .contact-item {
    display: flex;
    align-items: center;
    gap: 14px;
    height: 38px;
    font-size: 25px;
    color: var(--text-light);
  }
  .contact-icon {
    width: 20px;
    height: 20px;
    fill: var(--accent-red);
  }
</style>
</head>
<body>
<div class="canvas">
  <div class="card">
    <div class="accent-line"></div>
    <div class="dark-band" role="img" aria-label="Dark flowing wave decoration with a fine red accent"></div>

    <div class="brand">
      <span class="brand-square"></span>
      <span class="brand-name">KV Field Inspections</span>
    </div>

    <div class="person">
      <h1 class="person-name">MARCUS HALE</h1>
      <p class="person-title">CEO/Founder</p>
    </div>

    <ul class="contact">
      <li class="contact-item">
        <svg class="contact-icon" viewBox="0 0 24 24"><path d="M6.6 10.8c1.4 2.8 3.8 5.1 6.6 6.6l2.2-2.2c.3-.3.7-.4 1-.2 1.1.4 2.3.6 3.6.6.6 0 1 .4 1 1V20c0 .6-.4 1-1 1C10.6 21 3 13.4 3 4c0-.6.4-1 1-1h3.5c.6 0 1 .4 1 1 0 1.3.2 2.5.6 3.6.1.3 0 .7-.2 1z"/></svg>
        <span>555 210 4873</span>
      </li>
      <li class="contact-item">
        <svg class="contact-icon" viewBox="0 0 24 24"><path d="M2 5h20v14H2z M4 7v1l8 5 8-5V7l-8 5z" fill-rule="evenodd"/></svg>
        <span>marcus@kvfield.com</span>
      </li>
      <li class="contact-item">
        <svg class="contact-icon" viewBox="0 0 24 24"><path d="M12 2a10 10 0 1 0 0 20 10 10 0 0 0 0-20zm0 2c1 0 2.3 2 2.8 5H9.2C9.7 6 11 4 12 4zM9 11h6c0 .7 0 1.3-.1 2H9.1C9 12.3 9 11.7 9 11zm.2 4h5.6c-.5 3-1.8 5-2.8 5s-2.3-2-2.8-5z"/></svg>
        <span>www.kvfield.com</span>
      </li>
    </ul>
  </div>
</div>
</body>
</html>
```